Business card design for my company.
I would like the card's background colour to be black. You can also see our web site to get an idea of our brand. https://www.tmwhomecrafting.com.au/
- Name
- Email

```html
<!DOCTYPE html>
<html lang="en">
<head>
<meta charset="utf-8">
<title>TMW Home Crafting – Business Card</title>
<link rel="stylesheet" href="https://fonts.googleapis.com/css2?family=Montserrat:wght@400;500;700&display=swap">
<style>
  :root {
    --backdrop: #1b1b1b;
    --card-light: #f3f3f3;
    --card-dark: #171717;
    --brand-green: #069447;
    --brand-green-deep: #0b6a37;
    --ink: #1c1c1c;
    --white: #ffffff;
  }
  * { margin: 0; padding: 0; box-sizing: border-box; }
  html, body {
    width: 1200px; height: 1059px; overflow: hidden;
    background: var(--backdrop);
    font-family: "Montserrat", sans-serif;
  }
  .canvas { position: relative; width: 1200px; height: 1059px; }

  .card {
    position: absolute;
    width: 692px; height: 395px;
    border-radius: 26px;
    overflow: hidden;
  }
  .card-front { left: 255px; top: 89px; background: var(--card-light); }
  .card-back  { left: 253px; top: 546px; background: var(--brand-green); }

  .front-panel { position: absolute; inset: 0; width: 100%; height: 100%; }

  .holder-name {
    position: absolute; left: 26px; top: 42px;
    font-size: 30px; font-weight: 700; color: var(--brand-green);
    letter-spacing: 0.2px;
  }
  .holder-role {
    position: absolute; left: 26px; top: 82px;
    font-size: 17px; font-weight: 400; color: var(--ink);
    letter-spacing: 0.4px;
  }
  .holder-location {
    position: absolute; left: 26px; top: 178px;
    font-size: 17px; font-weight: 400; color: var(--ink);
    letter-spacing: 0.4px;
  }
  .contact-list {
    position: absolute; left: 26px; top: 268px;
    list-style: none;
  }
  .contact-item {
    display: flex; align-items: center; gap: 8px;
    height: 27.5px;
    font-size: 17px; font-weight: 400; color: var(--ink);
    letter-spacing: 0.3px;
  }
  .contact-icon { width: 16px; height: 16px; flex: none; }

  .front-brand {
    position: absolute; left: 468px; top: 150px; width: 200px;
    display: flex; align-items: center; gap: 10px;
    color: var(--white);
    font-size: 22px; font-weight: 700; line-height: 1.2;
    letter-spacing: 1px; text-transform: uppercase;
  }
  .brand-square {
    width: 14px; height: 14px; flex: none;
    background: var(--brand-green);
  }

  .back-brand {
    position: absolute; inset: 0;
    display: flex; align-items: center; justify-content: center;
    text-align: center;
    color: var(--brand-green-deep);
    font-size: 46px; font-weight: 700; line-height: 1.15;
    letter-spacing: 3px; text-transform: uppercase;
  }
</style>
</head>
<body>
<main class="canvas">

  <section class="card card-front" aria-label="Business card front">
    <svg class="front-panel" viewBox="0 0 692 395" preserveAspectRatio="none" aria-hidden="true">
      <path d="M482 0 C400 90 350 190 358 270 C364 330 385 370 404 395 L692 395 L692 0 Z" fill="var(--card-dark)"/>
      <path d="M531 0 L482 0 C420 70 370 160 370 250 C370 320 400 365 440 395 L408 395 C375 360 362 320 362 265 C362 170 420 70 500 0 Z" fill="var(--brand-green)"/>
      <path d="M440 395 C405 360 388 320 388 260 C388 195 410 150 440 110 C420 160 398 210 402 270 C406 320 430 365 462 395 Z" fill="var(--brand-green)"/>
    </svg>

    <h1 class="holder-name">Liam Hartley</h1>
    <p class="holder-role">General Manager</p>
    <p class="holder-location">Hobart, Tasmania, Australia</p>

    <ul class="contact-list">
      <li class="contact-item">
        <svg class="contact-icon" viewBox="0 0 16 16" aria-hidden="true">
          <path d="M1 6 C1 3 4 2 8 2 C12 2 15 3 15 6 L12 7 L11 5 L5 5 L4 7 Z" fill="var(--brand-green)"/>
          <rect x="3" y="8" width="10" height="6" rx="1" fill="var(--brand-green)"/>
        </svg>
        <span>0400 123 456</span>
      </li>
      <li class="contact-item">
        <svg class="contact-icon" viewBox="0 0 16 16" aria-hidden="true">
          <rect x="1" y="4" width="14" height="10" fill="var(--brand-green)"/>
          <path d="M1 4 L8 10 L15 4" fill="none" stroke="var(--card-light)" stroke-width="1.2"/>
        </svg>
        <span>info@tmwhomecrafting.com.au</span>
      </li>
      <li class="contact-item">
        <svg class="contact-icon" viewBox="0 0 16 16" aria-hidden="true">
          <circle cx="8" cy="8" r="7" fill="var(--brand-green)"/>
          <path d="M4 5 C6 4 7 6 6 8 C5 10 7 11 6 13 M10 3 C11 5 13 6 12 8 C11 10 12 11 11 13" fill="none" stroke="var(--card-light)" stroke-width="1.2"/>
        </svg>
        <span>www.tmwhomecrafting.com.au</span>
      </li>
    </ul>

    <div class="front-brand">
      <span class="brand-square" aria-hidden="true"></span>
      <span>TMW Home Crafting</span>
    </div>
  </section>

  <section class="card card-back" aria-label="Business card back">
    <p class="back-brand">TMW<br>Home Crafting</p>
  </section>

</main>
</body>
</html>
```